Membership Based Medical Practice Website

We need a functioning website for a new Membership based medical practice. There will be an enrollment fee and a monthly fee. We would like to see designs that are modern, simple. Should use neutral light colors. Examples of sites we like are www.kellanmoorclinic.com and https://fernholtcare.com/ We also have a link that when "Join Now" is clicked it will go to the signup website.

Target Market(s)

Gay Men, local population, Age group 20 to 60's.

Industry/Entity Type

Medical

Coding

Coded - Design and coding required

Number of Pages Required

5+ page

Font styles to use
Sans Serif

Colors
ffffff
cee9f5
ecf7fb
cfeae6
edf8f6
aaaaaa
e9e9e9
dbdbdb
fff3d1

Requirements
Must have
• Logo and header on every page. Clean, simple design, clear content, mobile compatible.
• Must use Wordpress
Nice to have
• Ideas should come from kellanmoorclinic.com
• Easy to read
Should not have
• Generic patient pictures, bold colors.
• Should not copy from above websites.

```html
<!DOCTYPE html>
<html lang="en">
<head>
<meta charset="utf-8">
<title>Larkfield Infectious Disease Specialists</title>
<link rel="stylesheet" href="https://fonts.googleapis.com/css2?family=Roboto+Condensed:wght@400;700&family=Open+Sans:wght@400;600&display=swap">
<style>
:root{
  --white:#ffffff;
  --sky:#cee9f5;
  --sky-light:#ecf7fb;
  --mint:#cfeae6;
  --mint-light:#edf8f6;
  --grey:#aaaaaa;
  --grey-light:#e9e9e9;
  --grey-mid:#dbdbdb;
  --cream:#fff3d1;
  --ink:#1b1b1b;
  --text:#444444;
  --gold:#c9b27a;
  --black:#000000;
}
*{margin:0;padding:0;box-sizing:border-box}
html,body{width:1200px;height:3922px;overflow:hidden}
body{position:relative;background:var(--white);font-family:'Open Sans',sans-serif;color:var(--text)}
.abs{position:absolute}
.heading{font-family:'Roboto Condensed',sans-serif;color:var(--ink)}

/* header */
.site-header{left:94px;top:0;width:1014px;height:100px;background:var(--white);border-radius:0 0 8px 8px;box-shadow:0 4px 14px rgba(0,0,0,.18);z-index:5;display:flex;align-items:center;padding:0 30px}
.brand{display:flex;align-items:center;gap:12px}
.brand-dot{width:18px;height:18px;border-radius:50%;background:var(--gold)}
.brand-name{font-family:'Open Sans',sans-serif;font-size:13px;letter-spacing:3px;color:var(--text);line-height:1.3}
.main-nav{margin-left:auto;display:flex;align-items:center;gap:36px;font-family:'Roboto Condensed',sans-serif;font-size:18px;color:var(--ink)}
.join-btn{background:var(--mint);padding:9px 22px;border-radius:3px;font-size:15px}

/* hero */
.hero{left:0;top:0;width:1200px;height:640px;background:linear-gradient(180deg,#c9cdd0 0%,#9aa39a 45%,#5b6a4a 62%,#3c3c3c 80%,#2a2a2a 100%)}
.hero-title{left:0;top:250px;width:1200px;text-align:center;font-size:74px;font-weight:700;color:var(--ink)}
.hero-sub{left:0;top:350px;width:1200px;text-align:center;font-size:52px;color:var(--white)}
.hero-arrow{top:340px;width:22px;height:22px;border-radius:50%;background:rgba(0,0,0,.55)}
.wave{left:0;width:1200px}

/* intro */
.intro-title{left:0;top:745px;width:1200px;text-align:center;font-size:33px;line-height:1.5;color:var(--ink)}
.intro-photo{left:136px;top:899px;width:356px;height:356px;border-radius:50%;background:radial-gradient(circle at 50% 45%,#f2f2f2 0%,#b9b3ad 30%,#7a2a2e 60%,#2d1a1d 100%);border:5px solid var(--cream)}
.expertise-title{left:585px;top:905px;font-size:32px}
.expertise-list{left:585px;top:962px;list-style:none;font-size:16px;line-height:33.5px;color:var(--text)}
.expertise-list li{display:flex;align-items:center;gap:18px}

/* pricing */
.pricing{left:0;top:1365px;width:1200px;height:687px;background:linear-gradient(180deg,#f1eef1 0%,#ece4ea 30%,#e6c9b5 62%,#c79a5c 82%,#7a5a2c 100%)}
.pricing-people{left:600px;top:1555px;width:490px;height:497px;background:linear-gradient(180deg,#8a7060 0%,#4d3a33 55%,#3a2c27 100%);border-radius:120px 120px 0 0;opacity:.85}
.pricing-title{left:0;top:1437px;width:1200px;text-align:center;font-size:36px;font-weight:700}
.pricing-sub{left:0;top:1488px;width:1200px;text-align:center;font-size:25px;color:var(--ink)}
.pricing-card{left:89px;top:1621px;width:507px;height:313px;background:rgba(255,255,255,.88);box-shadow:0 2px 10px rgba(0,0,0,.15);padding:38px 30px 0 60px}
.pricing-card ul{list-style:none;font-size:16px;line-height:22px;color:var(--ink)}
.pricing-card li{position:relative;margin-bottom:19px}
.pricing-card li::before{content:"";position:absolute;left:-34px;top:4px;width:14px;height:14px;border-radius:50%;border:2px solid var(--mint);background:var(--mint-light)}

/* features */
.features-title{left:0;top:2178px;width:1200px;text-align:center;font-size:35px;line-height:1.4;color:var(--ink)}
.feature{width:322px;height:392px}
.feature-photo{position:absolute;left:0;top:0;width:322px;height:240px}
.feature-card{position:absolute;left:13px;top:200px;width:296px;height:192px;background:var(--white);box-shadow:0 3px 10px rgba(0,0,0,.22);text-align:center;padding-top:48px}
.feature-card h3{font-family:'Roboto Condensed',sans-serif;font-weight:400;font-size:22px;color:var(--ink);margin-bottom:12px}
.feature-card p{font-size:13.5px;line-height:20px;padding:0 22px;color:var(--text);height:60px}
.read-more{display:inline-block;margin-top:12px;background:var(--sky);padding:5px 20px;border-radius:14px;font-size:13px;color:var(--ink)}
.dots{top:3247px;left:550px;display:flex;gap:20px}
.dots span{width:42px;height:3px;background:var(--sky)}
.dots span+span{background:var(--grey)}

/* footer */
.footer{left:0;top:3400px;width:1200px;height:522px;background:var(--black);color:var(--white)}
.newsletter-label{left:214px;top:3466px;font-family:'Roboto Condensed',sans-serif;font-size:30px;color:var(--white)}
.newsletter-form{left:418px;top:3463px;width:476px;height:44px;background:var(--white);border-radius:22px;overflow:hidden;display:flex}
.newsletter-form span{flex:1;font-size:13px;color:var(--grey);padding:13px 22px}
.newsletter-form b{background:var(--mint);font-weight:400;font-size:14px;color:var(--ink);padding:13px 20px}
.rule{left:83px;width:1020px;height:1px;background:#333}
.footer-brand{left:100px;top:3650px;width:200px;text-align:center}
.footer-brand .brand-dot{margin:0 auto 16px;width:40px;height:40px;background:transparent;border:2px solid var(--white)}
.footer-brand p{font-size:11px;letter-spacing:3px;line-height:1.5;color:var(--white)}
.footer-col h4{font-family:'Roboto Condensed',sans-serif;font-size:18px;letter-spacing:.5px;margin-bottom:16px}
.footer-col ul{list-style:none;font-size:13px;line-height:26px}
.footer-col li::before{content:"» ";}
.contact-list li::before{content:""}
.social{display:flex;gap:14px;margin-top:8px}
.social span{width:26px;height:26px;background:var(--white);border-radius:4px}
.copyright{left:0;top:3875px;width:1200px;text-align:center;font-size:13px;color:var(--white)}
</style>
</head>
<body>

<section class="hero abs" role="img" aria-label="Photo of an open country road stretching toward misty hills"></section>
<div class="hero-arrow abs" style="left:58px"><svg width="22" height="22" viewBox="0 0 22 22"><path d="M13 6 8 11l5 5" stroke="#fff" stroke-width="2" fill="none"/></svg></div>
<div class="hero-arrow abs" style="left:1126px"><svg width="22" height="22" viewBox="0 0 22 22"><path d="M9 6l5 5-5 5" stroke="#fff" stroke-width="2" fill="none"/></svg></div>
<h1 class="hero-title heading abs">Specialty medicine with</h1>
<p class="hero-sub heading abs">Commitment, Compassion and Care</p>
<svg class="wave abs" style="top:570px" width="1200" height="80" viewBox="0 0 1200 80" preserveAspectRatio="none">
  <path d="M0 40 Q300 90 600 50 T1200 30 V80 H0Z" fill="#cee9f5"/>
  <path d="M0 52 Q300 96 600 60 T1200 42 V80 H0Z" fill="#fff3d1"/>
  <path d="M0 62 Q300 100 600 68 T1200 52 V80 H0Z" fill="#ffffff"/>
</svg>

<header class="site-header abs">
  <div class="brand"><span class="brand-dot"></span><span class="brand-name">LARKFIELD<br>INFECTIOUS DISEASE SPECIALISTS</span></div>
  <nav class="main-nav"><span>Home</span><span>Specialties</span><span>Pricing</span><span>About Us</span><span>Faq</span><span>Blog</span><span class="join-btn">JOIN US</span></nav>
</header>

<h2 class="intro-title heading abs">We offer comprehensive treatment of a wide<br>variety of infectious diseases.</h2>
<div class="intro-photo abs" role="img" aria-label="Photo of a camping mug held in warm winter gloves"></div>
<h3 class="expertise-title heading abs" style="font-weight:400">Out expertise is in the following area.</h3>
<ul class="expertise-list abs">
  <li><svg width="22" height="10"><path d="M0 5h19M15 1l4 4-4 4" stroke="#9fd3c9" stroke-width="1.6" fill="none"/></svg>HIV/PrEP</li>
  <li><svg width="22" height="10"><path d="M0 5h19M15 1l4 4-4 4" stroke="#9fd3c9" stroke-width="1.6" fill="none"/></svg>Chronic Hepatitis</li>
  <li><svg width="22" height="10"><path d="M0 5h19M15 1l4 4-4 4" stroke="#9fd3c9" stroke-width="1.6" fill="none"/></svg>Sexually transmitted infections</li>
  <li><svg width="22" height="10"><path d="M0 5h19M15 1l4 4-4 4" stroke="#9fd3c9" stroke-width="1.6" fill="none"/></svg>Pre-travel vaccinations and counselling</li>
  <li><svg width="22" height="10"><path d="M0 5h19M15 1l4 4-4 4" stroke="#9fd3c9" stroke-width="1.6" fill="none"/></svg>Infections associated with medical devices</li>
  <li><svg width="22" height="10"><path d="M0 5h19M15 1l4 4-4 4" stroke="#9fd3c9" stroke-width="1.6" fill="none"/></svg>Bone and joint infections</li>
  <li><svg width="22" height="10"><path d="M0 5h19M15 1l4 4-4 4" stroke="#9fd3c9" stroke-width="1.6" fill="none"/></svg>Postsurgical infections</li>
  <li><svg width="22" height="10"><path d="M0 5h19M15 1l4 4-4 4" stroke="#9fd3c9" stroke-width="1.6" fill="none"/></svg>Diabetes related infections</li>
  <li><svg width="22" height="10"><path d="M0 5h19M15 1l4 4-4 4" stroke="#9fd3c9" stroke-width="1.6" fill="none"/></svg>Tuberculosis</li>
</ul>

<section class="pricing abs" role="img" aria-label="Photo of friends embracing in a field at sunset"></section>
<div class="pricing-people abs" role="img" aria-label="Group of friends seen from behind against the sunset"></div>
<h2 class="pricing-title heading abs">Our pricing is simple, transparent and affordable.</h2>
<p class="pricing-sub heading abs">Membership Plan $80/mo, plus a one-time $99 enrollment fee.</p>
<div class="pricing-card abs">
  <ul>
    <li>Includes all appointments, no co-pay</li>
    <li>Relaxed, unrushed visits</li>
    <li>Direct communication with your doctor via phone, email, video chat 24/7</li>
    <li>Convenient online scheduling (no need to call during business hours)</li>
    <li>Wholesale price for labs and medications</li>
  </ul>
</div>

<h2 class="features-title heading abs">Less wait, more personal.<br>We are not your traditional doctor's office.</h2>

<article class="feature abs" style="left:94px;top:2353px">
  <div class="feature-photo" role="img" aria-label="Photo of hikers walking toward snowy mountains" style="background:linear-gradient(180deg,#9cc3dd,#d9e3e6 45%,#6f7d55)"></div>
  <div class="feature-card"><h3>Straightforward pricing</h3><p>We charge all our patients the same low rate - no surprises.</p><span class="read-more">Read More</span></div>
</article>
<article class="feature abs" style="left:439px;top:2353px">
  <div class="feature-photo" role="img" aria-label="Photo of a person stretching in sunlit woods" style="background:linear-gradient(180deg,#d9d39a,#6f7b3a 55%,#2f3a22)"></div>
  <div class="feature-card"><h3>Hassle-free booking</h3><p>Schedule your appointment online at your convenience - no need to call during business hours.</p><span class="read-more">Read More</span></div>
</article>
<article class="feature abs" style="left:787px;top:2353px">
  <div class="feature-photo" role="img" aria-label="Photo of a person with open arms by the sea" style="background:linear-gradient(180deg,#cfe4f2,#a9cbe2 60%,#5f8fb3)"></div>
  <div class="feature-card"><h3>Devoted care</h3><p>We schedule enough time at each visit to make sure all of your questions are answered.</p><span class="read-more">Read More</span></div>
</article>
<article class="feature abs" style="left:94px;top:2802px">
  <div class="feature-photo" role="img" aria-label="Photo of friends hiking through a forest" style="background:linear-gradient(180deg,#c9b36a,#7c6a36 50%,#3b3520)"></div>
  <div class="feature-card"><h3>Save on medications</h3><p>We offer deeply discounted wholesale price medications for our members at pharmacy on site.</p><span class="read-more">Read More</span></div>
</article>
<article class="feature abs" style="left:439px;top:2802px">
  <div class="feature-photo" role="img" aria-label="Photo of a person leaping between rocks" style="background:linear-gradient(180deg,#f2f2f2,#c9c9c9 55%,#5e5e5e)"></div>
  <div class="feature-card"><h3>Save on lab costs</h3><p>If paying upfront for labs, we offer discounted pricing of up to 90% off standard rates.</p><span class="read-more">Read More</span></div>
</article>
<article class="feature abs" style="left:787px;top:2802px">
  <div class="feature-photo" role="img" aria-label="Photo from above of a person standing among green plants" style="background:linear-gradient(180deg,#3d5a3a,#27352b 60%,#1d2420)"></div>
  <div class="feature-card"><h3>Within your reach</h3><p>Follow-up appointments may be done by video chat for your convenience.</p><span class="read-more">Read More</span></div>
</article>
<div class="dots abs"><span></span><span></span></div>

<footer class="footer abs"></footer>
<svg class="wave abs" style="top:3340px" width="1200" height="90" viewBox="0 0 1200 90" preserveAspectRatio="none">
  <path d="M0 0 H1200 V40 Q900 0 600 40 T0 30Z" fill="#ffffff"/>
  <path d="M0 30 Q300 70 600 40 T1200 40 V50 Q900 10 600 50 T0 40Z" fill="#fff3d1"/>
  <path d="M0 40 Q300 80 600 50 T1200 50 V62 Q900 22 600 62 T0 52Z" fill="#cee9f5"/>
  <path d="M0 52 Q300 92 600 62 T1200 62 V90 H0Z" fill="#000000"/>
</svg>
<p class="newsletter-label abs">NEWSLETTER</p>
<div class="newsletter-form abs"><span>email@example.com</span><b>SUBSCRIBE</b></div>
<div class="rule abs" style="top:3568px"></div>
<div class="footer-brand abs"><div class="brand-dot"></div><p>LARKFIELD<br>INFECTIOUS DISEASE SPECIALISTS</p></div>
<div class="footer-col abs" style="left:376px;top:3632px">
  <h4>INFORMATION</h4>
  <ul><li>Privacy Policy</li><li>Your Account</li><li>Advanced Search</li><li>Contact Us</li></ul>
</div>
<div class="footer-col abs" style="left:596px;top:3632px">
  <h4>CONTACT US</h4>
  <ul class="contact-list"><li>Address : 412 Alder Row, Suite 210</li><li>Brookvale 40217</li><li>Phone : (555) 018-4470</li><li>Email : hello@larkfieldid.com</li></ul>
</div>
<div class="footer-col abs" style="left:889px;top:3627px">
  <h4>FOLLOW US OUT THERE</h4>
  <div class="social" aria-label="Social media links"><span></span><span></span><span></span><span></span></div>
</div>
<div class="rule abs" style="top:3832px"></div>
<p class="copyright abs">Copyright © 2019. All Rights Reserved</p>

</body>
</html>
```